Estate Agent Board Design

Most eye-catching, elegant estate agent board
Company logo should stand out
Korvimark & TREG should be small but visible.

On the board must be:

"FOR SALE"
logos
website zhbproperties.co.uk
tel number 01632 960418

It Company

```html
<!DOCTYPE html>
<html lang="en">
<head>
<meta charset="utf-8">
<title>ZHB Sales &amp; Lettings – For Sale Board</title>
<link href="https://fonts.googleapis.com/css2?family=Saira:wght@700;800&family=Roboto:wght@500;700&display=swap" rel="stylesheet">
<style>
  :root {
    --brand-green: #1d6b32;
    --brand-dark: #174a26;
    --board-white: #ffffff;
    --frame-grey: #8a8d90;
    --backdrop: #eef0ee;
    --text-dark: #1f2a22;
    --badge-blue: #1a5fb4;
    --badge-gold: #e2b92a;
  }
  * { margin: 0; padding: 0; box-sizing: border-box; }
  html, body { width: 1200px; height: 798px; overflow: hidden; }
  body { background: var(--backdrop); position: relative; font-family: "Roboto", Arial, sans-serif; }

  .board {
    position: absolute; left: 332px; top: 47px;
    width: 536px; height: 704px;
    background: var(--board-white);
    border: 5px solid var(--frame-grey);
    overflow: hidden;
  }
  .board__stripe {
    position: absolute; left: 0; top: 0; bottom: 0; width: 114px;
    background: var(--brand-green);
  }
  .board__stripe-rule {
    position: absolute; left: 120px; top: 0; bottom: 0; width: 6px;
    background: var(--brand-green);
  }
  .brand {
    position: absolute; left: 31px; top: 18px;
    width: 443px; height: 242px;
    background: var(--board-white);
    display: flex; flex-direction: column; justify-content: center; align-items: center;
  }
  .brand__name {
    font-family: "Saira", Arial, sans-serif; font-weight: 800;
    font-size: 132px; line-height: 1; letter-spacing: 6px;
    color: var(--brand-green);
  }
  .brand__tagline {
    margin-top: 6px;
    font-family: "Roboto", Arial, sans-serif; font-weight: 500;
    font-size: 24px; letter-spacing: 2px; color: var(--brand-green); white-space: nowrap;
  }
  .headline {
    position: absolute; left: 138px; top: 296px;
    font-family: "Saira", Arial, sans-serif; font-weight: 800;
    font-size: 90px; line-height: 0.9; color: var(--brand-dark);
  }
  .phone {
    position: absolute; left: 138px; top: 500px;
    display: flex; align-items: center; gap: 6px;
    font-family: "Saira", Arial, sans-serif; font-weight: 700;
    font-size: 38px; letter-spacing: 1.5px; color: var(--text-dark);
  }
  .phone svg { width: 28px; height: 34px; }
  .badges {
    position: absolute; left: 138px; top: 580px;
    display: flex; gap: 14px; align-items: center;
  }
  .badges svg { width: 62px; height: 62px; }
  .website {
    position: absolute; left: 114px; right: 0; top: 664px;
    text-align: center;
    font-size: 18px; letter-spacing: 3.5px; color: var(--text-dark);
  }
  .website strong { font-weight: 700; color: var(--brand-green); }
</style>
</head>
<body>
  <div class="board">
    <div class="board__stripe"></div>
    <div class="board__stripe-rule"></div>

    <div class="brand">
      <div class="brand__name">ZHB</div>
      <div class="brand__tagline">SALES &amp; LETTINGS</div>
    </div>

    <div class="headline">FOR<br>SALE</div>

    <div class="phone">
      <svg viewBox="0 0 24 30" aria-hidden="true">
        <path d="M6 2 L10 8 L7.5 11 C9 16 11 19 14 22 L17 19.5 L22 24 L18.5 28 C10 27 3 16 2 6 Z" fill="var(--brand-green)"/>
      </svg>
      <span>01632 960418</span>
    </div>

    <div class="badges">
      <svg viewBox="0 0 62 62" role="img" aria-label="Korvimark badge">
        <circle cx="31" cy="31" r="29" fill="var(--badge-blue)"/>
      </svg>
      <svg viewBox="0 0 62 62" role="img" aria-label="TREG badge">
        <circle cx="31" cy="31" r="28" fill="var(--board-white)" stroke="var(--badge-blue)" stroke-width="4"/>
        <circle cx="31" cy="31" r="16" fill="var(--badge-gold)"/>
      </svg>
    </div>

    <div class="website">www.<strong>zhbproperties</strong>.co.uk</div>
  </div>
</body>
</html>
```